Must Be Creative: Trade Show Booth for HR Conference 10x10

Design Style: high-level professional - a bit playful with our theme (read the theme) please be very creative...not boring...eye catching design that will make folks stop and think...We are going for bold. Look at the examples uploaded to this brief. Stick with clean designs professional.

Audience: HR and Talent Leaders

Size 10x10 - (114x91 - safe area 104x81)
we are not doing a podium - do not include it in your design.

Brand: Meridian Growth Studio - do not use our logo in the design. We will decide how and where to add the logo and QR code when we are done with the design. Make sure your design can accommodate a QR Code and our logo.

Brand Colors:
Navy Blue: #003366
Represents: Trust, stability, and professionalism.
Emerald Green: #009473
Represents: Growth, renewal, and prosperity. It also conveys a sense of balance and calm.
Deep Charcoal: #333333
Represents: Sophistication and strength, providing a solid background that makes other colors stand out.
Vibrant Orange: #FF6A00
Represents: Energy, enthusiasm, and warmth. It's an engaging color that can stimulate action and interaction.

FONT: bold face but soft font
Montserrat:
Roboto:
Lato:
Open Sans:

Theme Text:
Are Your Managers Driving Talent Away?
Tagline:
We Empower Leaders to Retain Talent

What we do: (Do not use "What we do text)
(This text can be included or excluded)
Equip Leaders
Engage Teams
Retain Top Talent
Ignite Inclusive Leadership

Imagine Must be Diverse Teams: (See images we uploaded)

Collaborative Teams: An image of a diverse group of professionals engaged in a collaborative work setting. This could be a roundtable discussion or a team actively engaging in a brainstorming session. Such an image would illustrate inclusivity and the dynamic interactions your training promotes.

Empowering Leadership: Consider an image that depicts a leader in action, possibly mentoring or guiding a team member. Showing a moment of teaching or a supportive interaction can powerfully convey the concept of "empower".

Inspirational Settings: An image that includes open, inviting workspace environments that suggest transparency and openness. Spaces that encourage free exchange of ideas can metaphorically represent an inclusive and engaging leadership style.

Success and Achievement: An image that captures a moment of celebration within a team—perhaps cheering or a congratulatory setting—can effectively illustrate the outcome of effective leadership and team retention.

Please ask any questions you have about this project. I've tried to paint the picture as well as I can.

Target Market(s)

HR and Talent Managers

Industry/Entity Type

Human Resources

Font styles to use
Serif
Sans Serif
Decorative

Colors
0054AA
0677BA
7BADD7
CADEEF
E8F1F8
0094D4
00A9DD
6FCCEA
C7EBF8
E9F6FB
00AB8E
00BBA5
67D7C9
C6EFE9
E9F9F6
F0912C
F2A743
F7CA91
FBE8D2
FDF5EE
EB3D1F
EC4F4E
F09395
F8D3D4
FCEDEE

Requirements
Must have
• creative design ideas
Nice to have
• incorporating the photo into the theme
Should not have
• Do not add our logo. We did not include it in the brief - we may add the logo later

```html
<!DOCTYPE html>
<html lang="en">
<head>
<meta charset="utf-8">
<title>Meridian Growth Studio – Trade Show Booth</title>
<link href="https://fonts.googleapis.com/css2?family=Montserrat:wght@700;800;900&family=Roboto:wght@700;900&display=swap" rel="stylesheet">
<style>
  :root {
    --navy: #003366;
    --emerald: #009473;
    --charcoal: #333333;
    --orange: #FF6A00;
    --white: #ffffff;
    --page: #ffffff;
    --floor-light: #eef1f4;
    --floor-mid: #cfd8e0;
    --glass: #a9bccd;
  }
  * { margin: 0; padding: 0; box-sizing: border-box; }
  html, body { width: 1200px; height: 2578px; overflow: hidden; background: var(--page); }
  .canvas { position: relative; width: 1200px; height: 2578px; }

  .booth {
    position: absolute; left: 99px; top: 785px;
    width: 1006px; height: 1007px; overflow: hidden;
    background: var(--white);
    box-shadow: 0 30px 60px rgba(0,0,0,0.18);
  }
  .booth__navy {
    position: absolute; left: 0; top: 0; width: 100%; height: 505px;
    background: var(--navy);
    border-bottom: 5px solid var(--emerald);
  }
  .theme-tab {
    position: absolute; left: 423px; top: 0; right: 0; height: 170px;
    background: var(--emerald);
    border-radius: 40px 0 0 40px;
    display: flex; flex-direction: column; justify-content: center;
    padding-left: 36px;
    font-family: 'Roboto', sans-serif; font-weight: 900;
    font-size: 44px; line-height: 51px; color: var(--white);
  }
  .brand-name {
    position: absolute; left: 92px; top: 44px; width: 310px;
    font-family: 'Montserrat', sans-serif; font-weight: 800;
    font-size: 40px; line-height: 44px; color: var(--white);
    text-transform: uppercase; letter-spacing: 1px;
  }
  .tagline {
    position: absolute; left: 0; top: 208px; width: 100%;
    text-align: center;
    font-family: 'Montserrat', sans-serif; font-weight: 900;
    font-size: 76px; line-height: 72px; color: var(--white);
    text-transform: uppercase; letter-spacing: 1px;
  }
  .scene-photo {
    position: absolute; left: 0; top: 620px; width: 100%; height: 387px;
    background:
      linear-gradient(to bottom, var(--white) 0%, rgba(255,255,255,0) 25%),
      linear-gradient(to bottom, var(--glass) 0%, var(--floor-light) 55%, var(--floor-mid) 100%);
  }
  .services { position: absolute; left: 0; top: 448px; width: 100%; }
  .service {
    position: absolute; width: 230px; margin-left: -115px;
    text-align: center;
  }
  .service__badge {
    width: 114px; height: 114px; margin: 0 auto;
    border-radius: 50%; background: var(--white);
    display: flex; align-items: center; justify-content: center;
  }
  .service__badge--green { border: 2px dotted var(--emerald); border-top: 7px solid var(--emerald); }
  .service__badge--navy { border: 8px solid var(--navy); border-top-color: var(--white); box-shadow: inset 0 0 0 2px var(--white); }
  .service__label {
    margin-top: 6px;
    font-family: 'Roboto', sans-serif; font-weight: 700;
    font-size: 25px; line-height: 31px; color: var(--charcoal);
  }
  .web-pill {
    position: absolute; left: 173px; top: 662px; width: 660px; height: 72px;
    border-radius: 36px; background: var(--orange);
    display: flex; align-items: center; justify-content: center;
    font-family: 'Roboto', sans-serif; font-weight: 700;
    font-size: 39px; letter-spacing: 3.5px; color: var(--white);
  }
</style>
</head>
<body>
<div class="canvas">
  <section class="booth">
    <div class="booth__navy"></div>
    <div class="scene-photo" role="img" aria-label="Photo of two colleagues sitting on the floor with laptops, talking in a bright open office"></div>

    <div class="brand-name">Meridian Growth Studio</div>
    <div class="theme-tab"><span>Are Your Managers</span><span>Driving Talent Away?</span></div>

    <h1 class="tagline">We Empower<br>Leaders to<br>Retain Talent</h1>

    <div class="services">
      <div class="service" style="left:205px">
        <div class="service__badge service__badge--green">
          <svg width="62" height="62" viewBox="0 0 62 62" fill="#333333">
            <circle cx="31" cy="12" r="7"/>
            <path d="M22 22h18v14H22z"/>
            <path d="M4 28c6 0 8 6 10 12l6 6h22l6-6c2-6 4-12 10-12v14l-12 14H16L4 42z"/>
          </svg>
        </div>
        <p class="service__label">Empower<br>Leaders</p>
      </div>
      <div class="service" style="left:395px">
        <div class="service__badge service__badge--navy">
          <svg width="62" height="62" viewBox="0 0 62 62" fill="#333333">
            <circle cx="14" cy="14" r="6"/><circle cx="31" cy="10" r="6"/><circle cx="48" cy="14" r="6"/>
            <path d="M6 24h16v10H6zM23 20h16v10H23zM40 24h16v10H40z"/>
            <path d="M6 38l14-4 10 6 12-6 14 4-8 12-18 4-16-6z"/>
          </svg>
        </div>
        <p class="service__label">Engage<br>Teams</p>
      </div>
      <div class="service" style="left:591px">
        <div class="service__badge service__badge--green">
          <svg width="64" height="64" viewBox="0 0 64 64" fill="none" stroke="#333333" stroke-width="4">
            <path d="M12 40A22 22 0 0 1 30 10"/><path d="M52 24A22 22 0 0 1 34 54"/>
            <path d="M26 6l6 4-5 6M38 58l-6-4 5-6"/>
            <g fill="#333333" stroke="none">
              <circle cx="22" cy="28" r="4"/><circle cx="32" cy="26" r="4"/><circle cx="42" cy="28" r="4"/>
              <path d="M16 34h12v8H16zM26 32h12v8H26zM36 34h12v8H36z"/>
            </g>
          </svg>
        </div>
        <p class="service__label">Retain<br>Top Talent</p>
      </div>
      <div class="service" style="left:790px">
        <div class="service__badge service__badge--navy">
          <svg width="62" height="62" viewBox="0 0 62 62" fill="#333333">
            <circle cx="14" cy="14" r="6"/><circle cx="31" cy="10" r="7"/><circle cx="48" cy="14" r="6"/>
            <path d="M6 22h16v20h-4v14h-8V42H6zM22 19h18v22h-4v16h-10V41h-4zM40 22h16v20h-4v14h-8V42h-4z"/>
          </svg>
        </div>
        <p class="service__label">Inspire Inclusive<br>Leadership</p>
      </div>
    </div>

    <div class="web-pill">meridiangrowthstudio.com</div>
  </section>
</div>
</body>
</html>
```